Wizards in Fibbing Crafts*

I am looking for a book cover which will really pop. Working title: Wizards in Fibbing Crafts (or W.F.C. for short) The concept behind the book is: education is too expensive, screwed up, and basically failing us, and even an MBA is not worth it's name anymore! How a BS is Brilliantly Stupid, a BA is great to be a Broke Artist, an MA is Mostly Antiquated and a MS Mastered Something? ...you get the point, basically I'll be ripping into a whole bunch of degree types, then walking you through what you should actually learn from an MBA. It is going to be written with a fair bit of humor, while still being fact driven. Target audience is working professionals who are considering an MBA, or have one and want a $15 refresher of all they spent $90k+ on. No color scheme is requested, Since i do like to allow creativity to flow!

Book size 5" by 8" and ebook. Author is: R.T. Halvorsen size format attached.

Went on vacation/holiday

• W.F.C. (but can be an emphasises in the Wizards in Fibbing Crafts title.
• If you look at "Side hustle blueprint: a guide toward cash liberty alongside a steady day job" on shopvale, you can see a blue/silver/white color scheme I liked in the past - but dont take that as a must by any means, the second choice was a completely different (red and white) scheme

```html
<!DOCTYPE html>
<html lang="en">
<head>
<meta charset="utf-8">
<title>W.F.C. – Wizards in Fibbing Crafts</title>
<link rel="stylesheet" href="https://fonts.googleapis.com/css2?family=Cinzel:wght@700;900&family=M+PLUS+Rounded+1c:wght@800&family=Libre+Baskerville&display=swap">
<style>
  :root {
    --ink-black: #000000;
    --cover-red: #9c0b10;
    --cover-red-deep: #5e0508;
    --paper-white: #ffffff;
    --print-dark: #1a0203;
  }
  html, body {
    margin: 0;
    padding: 0;
    width: 750px;
    height: 1200px;
    overflow: hidden;
    background: var(--ink-black);
  }
  .cover {
    position: relative;
    width: 750px;
    height: 1200px;
    background: var(--ink-black);
    overflow: hidden;
  }
  .cover-sweep {
    position: absolute;
    inset: 0;
    width: 750px;
    height: 1200px;
  }
  .acronym {
    position: absolute;
    top: 18px;
    left: 40px;
    right: 30px;
    display: flex;
    justify-content: space-between;
    align-items: flex-end;
    font-family: "M PLUS Rounded 1c", "Varela Round", sans-serif;
    font-weight: 800;
    font-size: 168px;
    line-height: 1;
    color: var(--paper-white);
  }
  .acronym .dot {
    display: inline-block;
    width: 34px;
    height: 34px;
    border-radius: 7px;
    background: var(--paper-white);
    margin-bottom: 30px;
  }
  .title {
    position: absolute;
    top: 196px;
    right: 40px;
    margin: 0;
    text-align: right;
    font-family: "Cinzel", serif;
    font-weight: 900;
    font-size: 56px;
    line-height: 75px;
    font-variant: small-caps;
    letter-spacing: 1px;
    color: var(--paper-white);
  }
  .title span { display: block; }
  .agree {
    position: absolute;
    top: 832px;
    left: 302px;
    transform: rotate(19deg);
    transform-origin: left top;
    display: flex;
    align-items: center;
    gap: 42px;
    font-family: "Libre Baskerville", serif;
    font-size: 58px;
    color: var(--print-dark);
  }
  .agree .box {
    width: 66px;
    height: 52px;
    border: 2px solid var(--print-dark);
    margin-top: 14px;
  }
  .author {
    position: absolute;
    right: 28px;
    bottom: 44px;
    margin: 0;
    font-family: "Cinzel", serif;
    font-weight: 900;
    font-size: 50px;
    font-variant: small-caps;
    letter-spacing: 1px;
    color: var(--paper-white);
    text-shadow: 0 8px 18px rgba(60, 0, 0, 0.7);
  }
</style>
</head>
<body>
<main class="cover">
  <svg class="cover-sweep" viewBox="0 0 750 1200" xmlns="http://www.w3.org/2000/svg">
    <defs>
      <linearGradient id="desk-tone" x1="0" y1="0" x2="1" y2="1">
        <stop offset="0" stop-color="var(--cover-red-deep)"/>
        <stop offset="0.35" stop-color="var(--cover-red)"/>
        <stop offset="1" stop-color="var(--cover-red)"/>
      </linearGradient>
    </defs>
    <path role="img" aria-label="Photograph of a pencil, ballpoint pen and fountain pen resting on a red sheet, tinted red"
          d="M0 254 C 250 262, 560 500, 750 800 L750 1200 L0 1200 Z"
          fill="url(#desk-tone)"/>
  </svg>

  <div class="acronym" aria-label="W.F.C.">
    <span>W</span><span class="dot"></span><span>F</span><span class="dot"></span><span>C</span><span class="dot"></span>
  </div>

  <h1 class="title">
    <span>Wizards in Fibbing</span>
    <span>Crafts</span>
  </h1>

  <div class="agree">
    <span>I Agree</span>
    <span class="box"></span>
  </div>

  <p class="author">R.T. Halvorsen</p>
</main>
</body>
</html>
```